Web Design For Manufacturing And Outsourcing Company

Pick up the pieces from our previous developer and help us complete our website.

5 pages - Home,Machining,Sourcing,About Us, and Contact

Attached you will find screen shots of previous direction but we're open to new ideas.

We can provide all text and images needed.

Thanks!

Number of Pages Required

5+ page

```html
<!DOCTYPE html>
<html lang="en">
<head>
<meta charset="utf-8">
<title>Kestrel Works – Home</title>
<link rel="stylesheet" href="https://fonts.googleapis.com/css2?family=Roboto:wght@400;500;700&family=Open+Sans:wght@400;600&display=swap">
<style>
:root{
  --orange:#ea4a1c;
  --orange-deep:#e0341a;
  --orange-light:#f07a32;
  --ink:#1d1d1d;
  --slate:#4a4a4c;
  --body:#333;
  --white:#fff;
  --mist:#e9e9ea;
}
*{margin:0;padding:0;box-sizing:border-box}
html,body{width:1200px;height:2990px;overflow:hidden;background:var(--white)}
.page{position:relative;width:1200px;height:2990px;overflow:hidden;font-family:"Open Sans",sans-serif;color:var(--body)}
.abs{position:absolute}
.brand{display:flex;align-items:center;gap:12px;font-family:"Roboto",sans-serif;font-weight:700;letter-spacing:3px;text-transform:uppercase}
.brand-dot{width:22px;height:22px;background:var(--orange)}
.btn{position:absolute;display:flex;align-items:center;justify-content:center;font-family:"Roboto",sans-serif;font-weight:500;font-size:17px;color:var(--white);text-transform:uppercase;letter-spacing:.5px;border-radius:2px}
.btn-orange{background:var(--orange)}
.btn-slate{background:var(--slate)}

/* hero */
.hero-photo{left:0;top:0;width:1200px;height:720px;background:radial-gradient(ellipse at 55% 40%,#8a8d92 0%,#4d5054 35%,#232428 70%,#111 100%)}
.nav{top:58px;left:500px;display:flex;gap:28px;font-family:"Roboto",sans-serif;font-weight:500;font-size:15px;color:var(--white);text-transform:uppercase}
.nav .active{color:var(--orange)}
.hero-title{top:260px;left:0;width:1200px;text-align:center;font-family:"Roboto",sans-serif;font-weight:700;font-size:38px;line-height:46px;color:var(--white);text-transform:uppercase}
.arrow{width:54px;height:54px;border-radius:50%;background:rgba(150,150,150,.55);display:flex;align-items:center;justify-content:center}

/* about */
.about-bg{left:0;top:700px;width:1200px;height:700px;background:linear-gradient(#fff 0%,#fff 35%,var(--mist) 100%)}
.h-section{font-family:"Roboto",sans-serif;font-weight:700;text-transform:uppercase;color:var(--ink)}
.quality{top:846px;left:0;width:1200px;text-align:center;font-family:"Roboto",sans-serif;font-weight:700;font-size:22px;color:var(--orange)}
.policy{top:884px;left:250px;width:700px;text-align:center;font-size:16px;line-height:28px;color:var(--ink)}
.value{width:240px;display:flex;gap:12px}
.value-icon{flex:none;width:52px;height:52px}
.value h4{font-family:"Roboto",sans-serif;font-weight:700;font-size:16px;color:var(--orange);text-transform:uppercase;margin-bottom:4px}
.value p{font-size:13px;line-height:19px;color:#444}
.value .more{display:block;margin-top:14px;font-family:"Roboto",sans-serif;font-weight:700;font-size:13px;color:#444;text-transform:uppercase}

/* sourcing */
.sourcing-text{left:162px;top:1486px;width:450px;color:var(--white)}
.sourcing-text h2{font-family:"Roboto",sans-serif;font-weight:700;font-size:34px;text-transform:uppercase;margin-bottom:10px}
.sourcing-text p{font-size:16px;line-height:27px}
.card{width:178px;height:172px;background:var(--white);box-shadow:0 2px 6px rgba(0,0,0,.25);display:flex;flex-direction:column;align-items:center;text-align:center;padding-top:10px}
.card svg{width:62px;height:62px}
.card h5{font-family:"Roboto",sans-serif;font-weight:700;font-size:19px;color:var(--slate);text-transform:uppercase;margin:6px 0 4px}
.card p{font-size:13px;line-height:17px;color:#444;width:120px}

/* machining */
.machining-text{left:610px;top:1996px;width:450px}
.machining-text h2{font-family:"Roboto",sans-serif;font-weight:700;font-size:34px;color:var(--ink);text-transform:uppercase;margin-bottom:12px}
.machining-text p{font-size:16px;line-height:27px;color:var(--ink)}

/* contact */
.cta-photo{left:0;top:2360px;width:1200px;height:480px;background:radial-gradient(ellipse at 65% 55%,#6a6c70 0%,#3b3d41 40%,#222326 80%)}
.cta-title{top:2540px;left:0;width:1200px;text-align:center;font-family:"Roboto",sans-serif;font-weight:400;font-size:32px;line-height:44px;color:var(--white);text-transform:uppercase}

/* footer */
.footer-nav{left:400px;top:2890px;display:flex;gap:18px;font-family:"Roboto",sans-serif;font-weight:500;font-size:15px;color:var(--ink);text-transform:uppercase}
.copyright{left:400px;top:2924px;font-family:"Roboto",sans-serif;font-weight:500;font-size:12px;color:#555}
.social{left:926px;top:2890px;display:flex;gap:9px}
.social span{width:30px;height:30px;border-radius:50%;display:block}
</style>
</head>
<body>
<div class="page">

  <!-- hero -->
  <header>
    <div class="abs hero-photo" role="img" aria-label="Close-up of a CNC machining centre with polished steel tooling"></div>
    <div class="abs brand" style="left:165px;top:54px;font-size:16px;color:var(--white)"><span class="brand-dot"></span>Kestrel Works</div>
    <nav class="abs nav"><span class="active">Home</span><span>Machining Capabilities</span><span>Sourcing</span><span>Contact Us</span></nav>
    <div class="abs arrow" style="left:96px;top:291px"><svg width="18" height="18" viewBox="0 0 18 18"><path d="M12 2 5 9l7 7" fill="none" stroke="#222" stroke-width="2.5"/></svg></div>
    <div class="abs arrow" style="left:1048px;top:291px"><svg width="18" height="18" viewBox="0 0 18 18"><path d="M6 2l7 7-7 7" fill="none" stroke="#222" stroke-width="2.5"/></svg></div>
    <h1 class="abs hero-title">A single point of contact for all<br>your procurement needs</h1>
    <a class="btn btn-orange" style="left:518px;top:374px;width:162px;height:46px">Read More</a>
  </header>

  <!-- about -->
  <div class="abs about-bg"></div>
  <svg class="abs" style="left:0;top:560px" width="1200" height="200" viewBox="0 560 1200 200">
    <path d="M0 690 C400 720 850 650 1200 570 L1200 760 L0 760Z" fill="var(--orange)"/>
    <path d="M0 706 C420 724 860 690 1200 640 L1200 760 L0 760Z" fill="#fff"/>
    <circle cx="600" cy="712" r="42" fill="#fff"/>
  </svg>

  <section>
    <h2 class="abs h-section" style="top:780px;left:0;width:1200px;text-align:center;font-size:34px">About Us</h2>
    <h3 class="abs quality">Quality Policy</h3>
    <p class="abs policy">We are committed to consistently exceeding customer expectations by providing products, services and sourcing solutions of the highest standard of quality. With our streamlined processes our method is efficient, provides value and ensures on time delivery. Our success isbased on continuously improving the efficiencies and effectiveness of our products</p>
    <h3 class="abs h-section" style="top:1036px;left:0;width:1200px;text-align:center;font-size:22px;font-weight:500">Core Values</h3>

    <div class="abs value" style="left:192px;top:1100px">
      <svg class="value-icon" viewBox="0 0 52 52" fill="none" stroke="var(--orange)" stroke-width="2.2"><circle cx="26" cy="14" r="6"/><circle cx="12" cy="20" r="5"/><circle cx="40" cy="20" r="5"/><path d="M16 40v-8a10 10 0 0 1 20 0v8M4 40v-6a8 8 0 0 1 10-7M48 40v-6a8 8 0 0 0-10-7"/></svg>
      <div><h4>Teamwork</h4><p>We are one company, one team. We understand when we work together we work smarter and not harder.</p><span class="more">Read More</span></div>
    </div>
    <div class="abs value" style="left:464px;top:1096px">
      <svg class="value-icon" viewBox="0 0 52 52" fill="none" stroke="var(--orange)" stroke-width="2.2"><path d="M26 44 8 28a10 10 0 0 1 14-14l4 4 4-4a10 10 0 0 1 14 14Z"/><path d="M18 30l8 6 8-8"/></svg>
      <div><h4>Respect</h4><p>We are one company, one team. We understand when we work together we work smarter and not harder.</p><span class="more">Read More</span></div>
    </div>
    <div class="abs value" style="left:790px;top:1094px">
      <svg class="value-icon" viewBox="0 0 52 52" fill="none" stroke="var(--orange)" stroke-width="2.2"><path d="M14 22V10h6v12M20 20V8h6v12M26 20V10h6v12M32 22V14h6v14c0 8-5 14-12 14h-2c-6 0-10-5-10-10V22Z"/></svg>
      <div><h4>Gratitude</h4><p>We appreciate where we have come from and the opportunities we are given to continue our journey.</p><span class="more">Read More</span></div>
    </div>
  </section>

  <!-- sourcing -->
  <svg class="abs" style="left:0;top:1300px" width="1200" height="640" viewBox="0 1300 1200 640">
    <defs><linearGradient id="sourcingFill" x1="0" x2="1"><stop offset="0" stop-color="var(--orange-deep)"/><stop offset="1" stop-color="var(--orange-light)"/></linearGradient></defs>
    <path d="M0 1390 C350 1330 800 1310 1200 1318 L1200 1360 L0 1420Z" fill="var(--slate)"/>
    <path d="M0 1412 C360 1350 800 1330 1200 1340 L1200 1800 C1000 1890 600 1910 0 1912Z" fill="url(#sourcingFill)"/>
    <path d="M1200 1760 L1200 1810 C980 1900 620 1915 0 1914 L0 1912 C600 1905 980 1880 1200 1760Z" fill="var(--slate)"/>
  </svg>

  <section>
    <div class="abs sourcing-text">
      <h2>Sourcing</h2>
      <p>Pellentesque faucibus Ut accumsan ultricies elit Maecenas at justo id velit placerat molestie Donec dictum lectus non odio Cras a ante vitae enim iaculis aliquam Mauris nunc quam venenatis nec euismod sit amet egestas placerat est Pellentesque habitant morbi tristique senectus et netus et malesuada fames ac turpis egestas Cras id elit</p>
    </div>
    <a class="btn btn-slate" style="left:164px;top:1720px;width:152px;height:44px">Read More</a>

    <div class="abs card" style="left:640px;top:1398px">
      <svg viewBox="0 0 62 62" fill="none" stroke="var(--orange)" stroke-width="2"><circle cx="31" cy="31" r="16"/><circle cx="31" cy="31" r="6"/><path d="M31 8v7M31 47v7M8 31h7M47 31h7M15 15l5 5M42 42l5 5M47 15l-5 5M15 47l5-5"/></svg>
      <h5>Vetting</h5><p>Donec dictum lectus non odio Cras</p>
    </div>
    <div class="abs card" style="left:834px;top:1438px">
      <svg viewBox="0 0 62 62" fill="none" stroke="var(--orange)" stroke-width="2"><circle cx="31" cy="31" r="22"/><path d="M31 18l4 9 9 1-7 6 2 9-8-5-8 5 2-9-7-6 9-1Z"/></svg>
      <h5>Quality</h5><p>Donec dictum lectus non odio Cras</p>
    </div>
    <div class="abs card" style="left:640px;top:1598px">
      <svg viewBox="0 0 62 62" fill="none" stroke="var(--orange)" stroke-width="2"><circle cx="31" cy="31" r="22"/><circle cx="31" cy="31" r="14"/><circle cx="31" cy="31" r="5"/></svg>
      <h5>Process</h5><p>Donec dictum lectus non odio Cras</p>
    </div>
    <div class="abs card" style="left:838px;top:1640px">
      <svg viewBox="0 0 62 62" fill="none" stroke="var(--orange)" stroke-width="2"><rect x="10" y="10" width="42" height="30"/><path d="M16 34l9-9 7 6 12-13M38 18h6v6M31 40v10M22 54l9-4 9 4"/></svg>
      <h5>Benefits</h5><p>Donec dictum lectus non odio Cras</p>
    </div>
  </section>

  <!-- contact band (drawn before hexagon so it sits beneath) -->
  <div class="abs cta-photo" role="img" aria-label="Dark close-up of a lathe spindle and cutting head"></div>
  <svg class="abs" style="left:0;top:2340px" width="1200" height="500" viewBox="0 2340 1200 500">
    <path d="M0 2340 H1200 V2420 C900 2370 500 2362 0 2372Z" fill="#fff"/>
    <path d="M640 2362 C900 2362 1080 2385 1200 2418 L1200 2436 C1080 2400 900 2376 640 2366Z" fill="var(--orange)"/>
    <path d="M0 2730 C300 2790 750 2820 1200 2780 L1200 2840 L0 2840Z" fill="var(--orange)"/>
    <path d="M0 2770 C300 2820 760 2840 1200 2800 L1200 2840 L0 2840Z" fill="#fff"/>
  </svg>

  <!-- machining -->
  <section>
    <svg class="abs" style="left:150px;top:1860px" width="400" height="512" viewBox="0 0 400 512">
      <polygon points="200,0 400,112 400,400 200,512 0,400 0,112" fill="#fff"/>
    </svg>
    <div class="abs" role="img" aria-label="Grinding wheel throwing sparks off a turned metal part" style="left:168px;top:1912px;width:364px;height:434px;clip-path:polygon(50% 0,100% 23%,100% 77%,50% 100%,0 77%,0 23%);background:radial-gradient(circle at 60% 60%,#f2a24a 0%,#3c7fc4 25%,#1d3f78 60%,#0d1c38 100%)"></div>
    <div class="abs machining-text">
      <h2>Machining</h2>
      <p>Pellentesque faucibus Ut accumsan ultricies elit Maecenas at justo id velit placerat molestie Donec dictum lectus non odio Cras a ante vitae enim iaculis aliquam Mauris nunc quam venenatis nec euismod sit amet egestas placerat est Pellentesque habitant morbi tristique senec</p>
    </div>
    <a class="btn btn-orange" style="left:612px;top:2224px;width:152px;height:44px">Read More</a>
  </section>

  <!-- contact -->
  <section>
    <div class="abs" style="left:590px;top:2484px;width:20px;height:20px;background:var(--white)"></div>
    <h2 class="abs cta-title">Contact us today with your machining<br>or sourcing needs!</h2>
    <a class="btn btn-orange" style="left:508px;top:2654px;width:202px;height:50px;font-size:18px">Get In Touch</a>
  </section>

  <!-- footer -->
  <footer>
    <div class="abs brand" style="left:135px;top:2890px;font-size:16px;color:var(--ink)"><span class="brand-dot"></span>Kestrel Works</div>
    <nav class="abs footer-nav"><span>Home</span><span>Machining Capabilities</span><span>Sourcing</span><span>Contact Us</span></nav>
    <p class="abs copyright">© 2019 Company Name &nbsp;All right reserved</p>
    <div class="abs social" aria-label="Social links">
      <span style="background:#3b5998"></span>
      <span style="background:#3ea1dd"></span>
      <span style="background:#3f6c94"></span>
      <span style="background:#1f7bb6"></span>
    </div>
  </footer>

</div>
</body>
</html>
```